Simple Logo Design for Semi-Clear Plastic Frosted Card stock

Create a business card on frosted plastic. compliment existing logo elements with a tree trunk, roots, or seed at the lower half and the full logo both on the front.

Contact information will go on a solid portion of the back of this design since this card stock is semi-transparent.

It is important to consider this plastic card stock medium in your design. I found helpful tips and guides listed at vellaprint-sample.net: be careful to understand ink printed on plastic cards cannot have too much of a consistent print area or risks peeling and fine lines can easily scratch off.
Updates

2" x 3.5" 20PT Clear Plastic Business cards with Round corners Please get info or templates here: https://www.vellaprint-sample.net/product-detail/2-x-35-20pt-clear-plastic-business-cards-with-round-corners

Target Market(s)

Not for profit- religion

Industry/Entity Type

Business

Must include complementary elements to the existing logo

Font styles to use
Decorative

Colors
000000

Requirements
Must have
• Elements of community, nature and oneness. Such as: seed, roots, tree trunk, etc.
• Three lines of space on the back for Name, Title, Phone Number.
Nice to have
• I like a light use of decorative elements
Should not have
• No eyes, from faces or animals.

```html
<!DOCTYPE html>
<html lang="en">
<head>
<meta charset="utf-8">
<title>Steadfast Grove – Business Card</title>
<link rel="stylesheet" href="https://fonts.googleapis.com/css2?family=Jost:wght@500&family=Libre+Baskerville:wght@700&family=Arimo:wght@400&display=swap">
<style>
  :root {
    --backdrop: #d6d6d4;
    --card-frost: #efefed;
    --teal-deep: #145449;
    --leaf-green: #2f8f34;
    --ink-light: #f4f6f4;
    --ink-soft: #cfe0da;
  }
  html, body {
    margin: 0;
    padding: 0;
    width: 1200px;
    height: 952px;
    overflow: hidden;
    background: var(--backdrop);
  }
  .card {
    position: absolute;
    left: 100px;
    top: 190px;
    width: 1000px;
    height: 571px;
    border-radius: 34px;
    background: var(--card-frost);
    overflow: hidden;
    box-shadow: 0 6px 18px rgba(0,0,0,0.12);
  }
  .card-wave {
    position: absolute;
    inset: 0;
    width: 1000px;
    height: 571px;
  }
  .brand {
    position: absolute;
    left: 100px;
    top: 100px;
    display: flex;
    align-items: center;
    gap: 20px;
    white-space: nowrap;
  }
  .brand-dot {
    width: 56px;
    height: 56px;
    border-radius: 50%;
    background: var(--leaf-green);
    flex: none;
  }
  .brand-name {
    font-family: "Jost", sans-serif;
    font-weight: 500;
    font-size: 48px;
    letter-spacing: 1px;
    color: var(--teal-deep);
    text-transform: uppercase;
  }
  .contact {
    position: absolute;
    right: 70px;
    top: 370px;
    text-align: right;
    color: var(--ink-light);
  }
  .contact-name {
    font-family: "Libre Baskerville", serif;
    font-weight: 700;
    font-size: 38px;
    line-height: 1.1;
  }
  .contact-title {
    font-family: "Arimo", sans-serif;
    font-size: 26px;
    color: var(--ink-soft);
    margin-top: 2px;
  }
  .contact-phone {
    margin-top: 52px;
    display: flex;
    align-items: center;
    justify-content: flex-end;
    gap: 18px;
    font-family: "Arimo", sans-serif;
    font-size: 32px;
  }
  .phone-icon {
    width: 26px;
    height: 34px;
  }
</style>
</head>
<body>
  <div class="card">
    <svg class="card-wave" viewBox="0 0 1000 571" aria-hidden="true">
      <path fill="var(--leaf-green)" d="M0,412 C200,542 380,502 520,332 C640,182 760,112 1000,107 L1000,571 L0,571 Z"/>
      <path fill="var(--teal-deep)" d="M0,430 C200,560 380,520 520,350 C640,200 760,130 1000,125 L1000,571 L0,571 Z"/>
    </svg>

    <div class="brand">
      <span class="brand-dot"></span>
      <span class="brand-name">Steadfast Grove</span>
    </div>

    <div class="contact">
      <div class="contact-name">Owen Harlow</div>
      <div class="contact-title">Director</div>
      <div class="contact-phone">
        <span>0412 555 318</span>
        <svg class="phone-icon" viewBox="0 0 26 34" aria-label="phone" role="img">
          <rect x="1" y="1" width="24" height="32" rx="3" fill="var(--ink-light)"/>
          <rect x="6" y="5" width="14" height="16" rx="1" fill="var(--teal-deep)"/>
          <circle cx="13" cy="27" r="2.5" fill="var(--teal-deep)"/>
        </svg>
      </div>
    </div>
  </div>
</body>
</html>
```